Media Services Start-up -- Corporate Website and Logo Design. Inspiration required!

We need a logo design and corporate website design, including coding, for our start-up business.
Vennatra’s value proposition is based on bringing together media content from a vast number of geographies globally, adding human and AI curation, translation and editing, and delivering the content using tailored customer interfaces. On the one hand, the business brings together media coverage from all over the world, and on the other it brings together content, human skills and technology to deliver a supreme customer experience.
Vennatra is a B2B media monitoring and analytics business with emphasis on global customers. Vennatra's service offering is centred around sourcing media content from different markets, processing, storing and delivering the content and insights derived from it using an online platform / mobile app.
The messaging we want to create through the logo is:
- Global scope
- Speed of delivery
- Cost-efficiency
- Multi-lingual
- Tailor-made
- Trustworthy
Target Market(s)
Business to business, PR / Communications, Media, Marketing
Logo Text
Vennatra
Coding
Coded - Design and coding required
Number of Pages Required
5+ page
Font styles to use
Other font styles liked:
- See Design Brief for details
Colors
Designer to choose colors to be used in the design.

```html
<!DOCTYPE html>
<html lang="en">
<head>
<meta charset="utf-8">
<title>Vennatra — Global Media Intelligence</title>
<link href="https://fonts.googleapis.com/css2?family=Roboto:wght@400;500;700&family=Ubuntu:wght@300;400;500&display=swap" rel="stylesheet">
<style>
:root{
  --coral:#f55a5a;
  --page-bg:#e8e8e8;
  --white:#ffffff;
  --ink:#222222;
  --body:#7a7a7a;
  --dark:#2d2d2d;
  --footer:#141414;
  --line:#d7d7d7;
  --nav-active:#7f9cf5;
}
*{margin:0;padding:0;box-sizing:border-box}
html,body{width:1200px;height:3236px;overflow:hidden;background:var(--page-bg)}
body{position:relative;font-family:'Ubuntu',sans-serif;color:var(--ink)}
.abs{position:absolute}
.page{position:absolute;left:44px;width:1131px;background:var(--white);overflow:hidden}
.page-home{top:34px;height:603px}
.page-solutions{top:658px;height:2545px}

.site-header{position:absolute;left:0;top:0;width:100%;height:55px;background:var(--coral)}
.brand{position:absolute;left:104px;top:0;line-height:55px;font-family:'Roboto',sans-serif;font-weight:700;font-size:20px;color:var(--white);letter-spacing:.2px}
.main-nav{position:absolute;right:105px;top:0;display:flex;gap:21px;line-height:55px}
.main-nav a{font-family:'Roboto',sans-serif;font-weight:700;font-size:14px;color:var(--white);text-decoration:none}
.main-nav a.active{color:var(--nav-active)}

.hero{position:absolute;left:0;top:55px;width:100%;height:495px;background:linear-gradient(135deg,#1d2b38 0%,#2a3f4d 30%,#3a3a3a 60%,#26323b 100%)}
.hero-photo{position:absolute;inset:0;background:radial-gradient(ellipse at 60% 40%,rgba(70,110,130,.55),rgba(0,0,0,0) 60%),linear-gradient(180deg,rgba(0,0,0,0) 70%,#2e2e2e 100%)}
.hero-title{position:absolute;left:112px;top:120px;font-family:'Roboto',sans-serif;font-weight:700;font-size:32px;line-height:52px;color:var(--white)}
.hero-copy{position:absolute;left:112px;top:243px;width:408px;font-size:17.5px;line-height:29px;color:var(--white);text-align:justify}
.lead-card{position:absolute;left:623px;top:108px;width:381px;height:391px;background:var(--white)}
.lead-card h3{position:absolute;left:48px;top:66px;font-family:'Roboto',sans-serif;font-weight:700;font-size:13px;color:var(--ink)}
.field{position:absolute;left:48px;width:286px;height:40px;border:2px solid var(--line);border-radius:3px;display:flex;align-items:center;padding-left:17px;gap:7px;font-size:13px;color:#888}
.field svg{width:12px;height:12px;fill:#888}
.btn{position:absolute;left:49px;top:317px;width:128px;height:40px;background:var(--coral);border-radius:3px;color:var(--white);font-family:'Roboto',sans-serif;font-weight:700;font-size:14px;line-height:40px;text-align:center}
.copyright{position:absolute;right:117px;top:569px;font-family:'Roboto',sans-serif;font-size:13px;color:#555}

.banner{position:absolute;left:0;top:56px;width:100%;height:254px;background:linear-gradient(100deg,#c9c2ba 0%,#a59583 35%,#b9a794 60%,#8d8a85 100%)}
.banner-title{position:absolute;left:0;top:86px;width:100%;text-align:center;font-family:'Roboto',sans-serif;font-weight:700;font-size:50px;color:var(--white);text-shadow:0 2px 8px rgba(0,0,0,.45)}

.section h2{font-family:'Roboto',sans-serif;font-weight:700;font-size:25px;color:var(--ink);margin-bottom:14px}
.section .intro{font-size:15px;line-height:26px;color:var(--ink);margin-bottom:8px}
.section ul{list-style:none}
.section li{font-size:14px;line-height:26.5px;color:var(--body);text-align:justify}
.tick{display:inline-block;width:12px;height:12px;vertical-align:-1px;margin-right:6px}
.photo{position:absolute;width:361px;height:252px}
.photo::before{content:"";position:absolute;left:-8px;top:-8px;width:352px;height:244px;background:#555;border-radius:10px}
.photo .fill{position:absolute;inset:0;border-radius:10px}

.site-footer{position:absolute;left:0;top:2310px;width:100%;height:235px;background:var(--footer);color:var(--white);text-align:center}
.footer-brand{position:absolute;left:0;top:42px;width:100%;font-family:'Roboto',sans-serif;font-weight:700;font-size:27px}
.footer-nav{position:absolute;left:0;top:98px;width:100%;font-size:14.5px}
.footer-nav span.sep{margin:0 14px}
.footer-contact{position:absolute;left:0;top:142px;width:100%;font-size:14.5px;display:flex;justify-content:center;gap:36px}
.footer-contact svg{width:12px;height:12px;fill:var(--white);vertical-align:-1px;margin-right:6px}
.footer-copy{position:absolute;left:0;top:192px;width:100%;font-size:13.5px}
</style>
</head>
<body>
<svg width="0" height="0" style="position:absolute">
  <symbol id="tick" viewBox="0 0 12 12"><circle cx="6" cy="6" r="5" fill="none" stroke="#f55a5a" stroke-width="1.6"/><path d="M3.5 6.2l1.7 1.7 3.3-3.5" fill="none" stroke="#f55a5a" stroke-width="1.6"/></symbol>
</svg>

<div class="page page-home">
  <header class="site-header">
    <div class="brand">VENNATRA</div>
    <nav class="main-nav"><a>Home</a><a>About Us</a><a>Solutions</a><a>How We Do It</a><a>Our People</a><a>Our Technology</a><a>Contact Us</a></nav>
  </header>
  <section class="hero">
    <div class="hero-photo" role="img" aria-label="Wall of glowing media screens with a figure standing in front"></div>
    <h1 class="hero-title">DELIVERING GLOBAL<br>MEDIA INTELLIGENCE</h1>
    <p class="hero-copy">Vennatra is an international media intelligence service provider. We help communications teams build and operate truly global media monitoring and measurement programmes.</p>
    <form class="lead-card">
      <h3>LEARN MORE ABOUT VENNATRA</h3>
      <div class="field" style="top:105px"><svg viewBox="0 0 12 12"><circle cx="6" cy="3.5" r="3"/><path d="M0 12c0-4 3-5.5 6-5.5s6 1.5 6 5.5z"/></svg>Enter Your Name</div>
      <div class="field" style="top:161px"><svg viewBox="0 0 12 12"><path d="M0 2h12v1.5L6 7 0 3.5z M0 5l6 3.5L12 5v6H0z"/></svg>Enter Your Email</div>
      <div class="field" style="top:218px"><svg viewBox="0 0 12 12"><path d="M2.5 0l2 3-1.2 1.5c.8 1.7 2.2 3 4 4L8.5 7.3l3 2L10 12C5 11.5.5 7 0 2z"/></svg>Enter Your Phone No</div>
      <div class="btn">GET STARTED</div>
    </form>
  </section>
  <p class="copyright">© 2019 Vennatra. All Rights Reserved</p>
</div>

<div class="page page-solutions">
  <header class="site-header">
    <div class="brand">VENNATRA</div>
    <nav class="main-nav"><a>Home</a><a>About Us</a><a class="active">Solutions</a><a>How We Do It</a><a>Our People</a><a>Our Technology</a><a>Contact Us</a></nav>
  </header>
  <section class="banner" role="img" aria-label="Hands working on a tablet and laptop with chart overlays">
    <h1 class="banner-title">SOLUTIONS</h1>
  </section>

  <section class="section abs" style="left:103px;top:388px;width:476px">
    <h2>CONTENT SOURCING</h2>
    <p class="intro">We help you build a content strategy that meets your budget and coverage needs across earned media - Print, Online, TV and Radio.</p>
    <ul>
      <li><svg class="tick"><use href="#tick"/></svg>Identify geographies and markets of interest</li>
      <li><svg class="tick"><use href="#tick"/></svg>Build target media source lists to fulfil monitoring and measurement requirements</li>
      <li><svg class="tick"><use href="#tick"/></svg>Using our transparent cost calculator, we help you with accurate budgeting and choices to ensure you meet your strategy and objectives</li>
      <li><svg class="tick"><use href="#tick"/></svg>Translate and localise keyword searches and editorial instructions into effecient source-/ country-/ provider-specific needs to minimise wasted content.</li>
    </ul>
  </section>
  <div class="photo" style="left:673px;top:436px"><div class="fill" role="img" aria-label="Man in glasses reading a book at a desk" style="background:linear-gradient(135deg,#b48a68,#7a5a45 50%,#d6c2ad)"></div></div>

  <div class="photo" style="left:111px;top:763px"><div class="fill" role="img" aria-label="Businesswoman with laptop before a digital data city" style="background:linear-gradient(135deg,#4b6be0,#2a2f9a 55%,#1a1f6e)"></div></div>
  <section class="section abs" style="left:548px;top:827px;width:476px">
    <h2>CONTENT COLLECTION</h2>
    <ul>
      <li><svg class="tick"><use href="#tick"/></svg>We consolidate and manage the delivery of your global media content into a Cloud-based scalable media platform, taking the headache of content management away from your teams.</li>
    </ul>
  </section>

  <section class="section abs" style="left:103px;top:1077px;width:476px">
    <h2>CONTENT AUGMENTATION</h2>
    <ul style="margin-top:30px">
      <li><svg class="tick"><use href="#tick"/></svg>We manage and normalise all of the source-level reference data - country, language, reach etc.</li>
      <li><svg class="tick"><use href="#tick"/></svg>We add editorial validation to ensure only the content required reaches your delivery, removing inevitable noise from source providers</li>
      <li><svg class="tick"><use href="#tick"/></svg>Tagging - AI and human based tagging to detect locations, people, topics, products, brands, services, etc.</li>
      <li><svg class="tick"><use href="#tick"/></svg>Human and automated grouping of stories across geographies - clustering, "also-in" groupings etc.</li>
      <li><svg class="tick"><use href="#tick"/></svg>Translation summarisation - AI Translation or human-created depending on budget, speed of delivery and need.</li>
      <li><svg class="tick"><use href="#tick"/></svg>Digest authoring - refining the essence of today's coverage into a concise board-ready output for your organisation</li>
    </ul>
  </section>
  <div class="photo" style="left:673px;top:1138px"><div class="fill" role="img" aria-label="Two colleagues reviewing a dashboard on a laptop" style="background:linear-gradient(135deg,#e9e6e0,#b9b3ab 50%,#3e4a68)"></div></div>

  <div class="photo" style="left:111px;top:1517px"><div class="fill" role="img" aria-label="Woman at an office desk with shelves and boxes" style="background:linear-gradient(135deg,#f2efe8,#e3d6c2 50%,#cfc4b6)"></div></div>
  <section class="section abs" style="left:548px;top:1494px;width:478px">
    <h2>CONTENT DELIVERY</h2>
    <p class="intro">Early morning delivery of a consolidated, ready-to-consume media coverage</p>
    <ul>
      <li><svg class="tick"><use href="#tick"/></svg>Customised email templates, delivering content in templates designed to meet your needs</li>
      <li><svg class="tick"><use href="#tick"/></svg>Customised platform - modern portal tailored to meet your media management needs, removing the unwanted clutter and focusing on the job at hand</li>
      <li><svg class="tick"><use href="#tick"/></svg>Integration with Intranets, third-party communication tools e.g. Chatterly, RSS readers, customised APIs</li>
    </ul>
  </section>

  <section class="section abs" style="left:103px;top:1837px;width:476px">
    <h2>MEDIA INSIGHTS &amp; CONSULTANCY</h2>
    <ul style="margin-top:30px">
      <li><svg class="tick"><use href="#tick"/></svg>Levering the normalised content sets from your integrated monitoring service, we can analyse and tag your coverage based on complex qualitative measurement criteria, consistent across all languages and geographies, to combine with quantitative metrics.</li>
      <li><svg class="tick"><use href="#tick"/></svg>Ability to create a single consistent measurement programme across all of your global operations.</li>
      <li><svg class="tick"><use href="#tick"/></svg>Consultancy to HQ and local offices on how to utilise and align existing measurement and insight intiatives to provide continuity.</li>
      <li><svg class="tick"><use href="#tick"/></svg>Customised online dashboards with near real time data insights, coupled with Board-ready offline reporting and export options.</li>
      <li><svg class="tick"><use href="#tick"/></svg>Integration with social media content, third-party data, point-of-sale, WebMetrics, and delivering on your Integrated Communications Framework</li>
    </ul>
  </section>
  <div class="photo" style="left:673px;top:1923px"><div class="fill" role="img" aria-label="Business meeting at a table with papers and coffee" style="background:linear-gradient(135deg,#d9d9d6,#8c8c88 50%,#eeeeec)"></div></div>

  <footer class="site-footer">
    <div class="footer-brand">VENNATRA</div>
    <div class="footer-nav">Home<span class="sep">|</span>About Us<span class="sep">|</span>Solutions<span class="sep">|</span>How We Do It<span class="sep">|</span>Our People<span class="sep">|</span>Our Technology<span class="sep">|</span>Contact Us</div>
    <div class="footer-contact">
      <span><svg viewBox="0 0 12 12"><path d="M6 0a4 4 0 0 0-4 4c0 3 4 8 4 8s4-5 4-8a4 4 0 0 0-4-4zm0 5.5A1.5 1.5 0 1 1 6 2.5a1.5 1.5 0 0 1 0 3z"/></svg>Neque porro quisquam est, qui dolorem</span>
      <span><svg viewBox="0 0 12 12"><path d="M2.5 0l2 3-1.2 1.5c.8 1.7 2.2 3 4 4L8.5 7.3l3 2L10 12C5 11.5.5 7 0 2z"/></svg>888 888 8888</span>
      <span><svg viewBox="0 0 12 12"><path d="M0 2h12v8H0z M1.2 3.2v.3L6 6.8l4.8-3.3v-.3z M1.2 5v3.8h9.6V5L6 8.2z" fill-rule="evenodd"/></svg>info@vennatra.com</span>
    </div>
    <div class="footer-copy">© 2019 Vennatra. All Rights Reserved</div>
  </footer>
</div>
</body>
</html>
```